Quillmere Supply Chain and Logistic Consulting

Please review the attached Business Card. I want as close to this card with the colors, fonts, and quality of the card as possible. The attached compass should replace the deer head on both sides of the card and the text should say:

Backside
Compass JPEG
Quillmere Partners
A Supply Chain and Logistics Consulting Company

Frontside
Quillmere Partners
Ray Falkner - Lakeport Ohio
President
____________________________________
(555) 314-9027
QuillmereSCL@Examplemail.com
_____________________________________

Bottom Front Side

Target Market(s)

Businesses

Contact Information for Business Card

Backside
Compass JPEG
Quillmere Partners

Frontside
Quillmere Partners
President
(555) 314-9027
QuillmereSCL@Examplemail.com

Bottom Front Side

Font styles to use
Serif
Script

Colors

Designer to choose colors to be used in the design.

Requirements
Must have
• See attached card for reference
Nice to have
Should not have

```html
<!DOCTYPE html>
<html lang="en">
<head>
<meta charset="UTF-8">
<title>Quillmere Partners – Business Card</title>
<link rel="stylesheet" href="https://fonts.googleapis.com/css2?family=Cinzel:wght@400;500&display=swap">
<style>
  :root {
    --backdrop: #2b2b2d;
    --card: #141415;
    --card-edge: #1f1f21;
    --silver: #d4d4d4;
    --silver-soft: #a9a9a9;
    --silver-dim: #7c7c7c;
    --rule: #8f8f8f;
    --mark: #b9b9b9;
  }
  * { margin: 0; padding: 0; box-sizing: border-box; }
  html, body {
    width: 1200px;
    height: 900px;
    overflow: hidden;
    background: var(--backdrop);
    font-family: "Cinzel", "Times New Roman", serif;
  }
  .canvas {
    position: relative;
    width: 1200px;
    height: 900px;
  }
  .card {
    position: absolute;
    left: 290px;
    width: 620px;
    height: 354px;
    background: var(--card);
    border: 1px solid var(--card-edge);
    color: var(--silver);
    text-align: center;
  }
  .card--front { top: 66px; }
  .card--back { top: 480px; }

  .card h1, .card h2 { font-weight: 400; }

  /* Front side */
  .front-company {
    position: absolute;
    top: 36px;
    width: 100%;
    font-size: 30px;
    letter-spacing: 1.5px;
  }
  .front-name {
    position: absolute;
    top: 86px;
    width: 100%;
    font-size: 17px;
    letter-spacing: 1px;
  }
  .front-title {
    position: absolute;
    top: 114px;
    width: 100%;
    font-size: 13px;
    letter-spacing: 1px;
    color: var(--silver-soft);
  }
  .contact-rule {
    position: absolute;
    left: 150px;
    width: 320px;
    height: 1px;
    background: linear-gradient(90deg, transparent, var(--rule) 30%, var(--rule) 70%, transparent);
  }
  .contact-rule--top { top: 146px; }
  .contact-rule--bottom { top: 212px; }
  .front-phone {
    position: absolute;
    top: 158px;
    width: 100%;
    font-size: 14px;
    letter-spacing: 1px;
  }
  .front-email {
    position: absolute;
    top: 182px;
    width: 100%;
    font-size: 13px;
    letter-spacing: 1px;
  }
  .social-row {
    position: absolute;
    top: 226px;
    left: 0;
    width: 100%;
    display: flex;
    justify-content: center;
    gap: 14px;
  }
  .social-badge {
    width: 15px;
    height: 15px;
    background: var(--silver);
    border-radius: 2px;
  }
  .front-tagline {
    position: absolute;
    top: 290px;
    left: 30px;
    right: 30px;
    display: flex;
    align-items: center;
    gap: 14px;
    font-size: 12px;
    letter-spacing: 1px;
    color: var(--silver-soft);
    white-space: nowrap;
  }
  .tagline-rule {
    flex: 1;
    height: 1px;
    background: var(--rule);
  }

  /* Back side */
  .back-mark {
    position: absolute;
    top: 48px;
    left: 250px;
    width: 120px;
    height: 120px;
    border-radius: 50%;
    background: var(--mark);
  }
  .back-company {
    position: absolute;
    top: 196px;
    width: 100%;
    font-size: 32px;
    letter-spacing: 2px;
    color: var(--silver-soft);
  }
  .back-tagline {
    position: absolute;
    top: 246px;
    width: 100%;
    font-size: 12px;
    letter-spacing: 1px;
    color: var(--silver-dim);
  }
</style>
</head>
<body>
<main class="canvas">

  <section class="card card--front" aria-label="Business card front">
    <h1 class="front-company">Quillmere Partners</h1>
    <p class="front-name">Ray Falkner • Lakeport Ohio</p>
    <p class="front-title">president</p>
    <div class="contact-rule contact-rule--top"></div>
    <p class="front-phone">(555) 314-9027</p>
    <p class="front-email">QuillmereSCL@Examplemail.com</p>
    <div class="contact-rule contact-rule--bottom"></div>
    <div class="social-row" aria-label="Social profiles">
      <span class="social-badge"></span>
      <span class="social-badge"></span>
      <span class="social-badge"></span>
    </div>
    <p class="front-tagline">
      <span class="tagline-rule"></span>
      A Supply Chain and Logistics Consulting Company
      <span class="tagline-rule"></span>
    </p>
  </section>

  <section class="card card--back" aria-label="Business card back">
    <div class="back-mark" aria-hidden="true"></div>
    <h2 class="back-company">Quillmere Partners</h2>
    <p class="back-tagline">A Supply Chain and Logistics Consulting Company</p>
  </section>

</main>
</body>
</html>
```